Electrical Contractor Brochure, Folder and Letter Head

Brightwell Power Ltd. is an Edmonton based electrical contractor focusing on commercial and industrial electrical services. Our target market is manufacturing facilities, warehouses and commercial buildings.

We want to seem larger than we are with service vehicles and electricians ready to dispatch to service calls and new installations. Our key color is the blue in the logo. The BWP logo is well branded in Edmonton and should be on the brochure.

We are looking for a tri-fold brochure, full-page brochure with folder sleeves and a letter head.
Updates

Please ignore the second page of copy.  I only want the electrical content in the brochure.  This is my mistake.  Please use only the first page of copy.

Industry/Entity Type

Electrical

Requirements
Must have
• Many background pics of the services, electricians and projects. I like the faded BWP logo in the background of the letterhead! Folder Size A4
Nice to have
• Try the pic named Cover Pic1 to on the front of the brochure.
Should not have
• DO NOT USE ANY WEBSITE CONTENT. THIS IS NOT OUR BUSINESS. PLEASE USE ONLY CONTENT AND COLOR FROM THE ATTACHED FILES!!

```html
<!DOCTYPE html>
<html lang="en">
<head>
<meta charset="utf-8">
<title>Brightwell Power Ltd. — Letterhead</title>
<link rel="stylesheet" href="https://fonts.googleapis.com/css2?family=Source+Sans+3:wght@400;700;800&display=swap">
<style>
  :root {
    --brand-blue: #1a5ea8;
    --brand-blue-dark: #1c3f87;
    --swoosh-grey: #7b7b7b;
    --ink: #3a3a3a;
    --rule: #c9c9c9;
    --watermark: #edf1f6;
    --paper: #ffffff;
  }
  * { margin: 0; padding: 0; box-sizing: border-box; }
  html, body { width: 1011px; height: 1200px; overflow: hidden; background: var(--paper); }
  body { font-family: "Source Sans 3", Arial, sans-serif; color: var(--ink); }

  .letterhead { position: relative; width: 1011px; height: 1200px; background: var(--paper); overflow: hidden; }

  .brand-name {
    position: absolute; left: 73px; top: 58px;
    font-size: 40px; font-weight: 800; line-height: 1.05;
    color: var(--brand-blue-dark); letter-spacing: 0.5px;
    width: 330px;
  }

  .contact-block {
    position: absolute; left: 801px; top: 57px; height: 102px;
    border-left: 1px solid var(--rule);
    padding-left: 15px;
    font-size: 15px; line-height: 17px;
  }
  .contact-address { margin-top: 1px; }
  .contact-list { list-style: none; margin-top: 13px; }
  .contact-list li { display: flex; align-items: center; gap: 5px; height: 19px; }
  .contact-icon { width: 11px; height: 11px; flex: none; }

  .watermark {
    position: absolute; left: 0; right: 0; top: 440px;
    text-align: center;
    font-size: 280px; font-weight: 800; line-height: 1;
    color: var(--watermark); letter-spacing: 6px;
    user-select: none;
  }

  .footer-wave { position: absolute; left: 0; top: 1080px; width: 1011px; height: 120px; }
  .footer-url {
    position: absolute; left: 726px; top: 1165px;
    font-size: 16px; letter-spacing: 3px; color: #ffffff;
  }
</style>
</head>
<body>
  <div class="letterhead">
    <div class="brand-name">Brightwell Power Ltd.</div>

    <div class="contact-block">
      <p class="contact-address">00, complex name<br>City, state</p>
      <ul class="contact-list">
        <li>
          <svg class="contact-icon" viewBox="0 0 12 12" aria-hidden="true"><circle cx="6" cy="6" r="5" fill="none" stroke="var(--brand-blue)" stroke-width="1.3"/><path d="M4 3.5 Q3.5 7 7.5 8.5" fill="none" stroke="var(--brand-blue)" stroke-width="1.5"/></svg>
          123-456-0789
        </li>
        <li>
          <svg class="contact-icon" viewBox="0 0 12 12" aria-hidden="true"><rect x="3" y="1" width="6" height="4" fill="var(--brand-blue)"/><rect x="1" y="5" width="10" height="5" rx="1" fill="var(--brand-blue)"/></svg>
          123-456-0789
        </li>
        <li>
          <svg class="contact-icon" viewBox="0 0 12 12" aria-hidden="true"><rect x="1" y="3" width="10" height="7" fill="var(--brand-blue)"/><path d="M1 3 L6 7 L11 3" fill="none" stroke="#fff" stroke-width="1"/></svg>
          info@brightwellpower.com
        </li>
      </ul>
    </div>

    <div class="watermark" aria-hidden="true">BWP</div>

    <svg class="footer-wave" viewBox="0 0 1011 120" preserveAspectRatio="none" aria-hidden="true">
      <path fill="var(--swoosh-grey)" d="M0,9 C120,60 300,72 480,62 C650,52 800,44 860,47 C930,50 980,66 1011,81 L1011,84 C930,64 820,60 700,64 C500,72 300,90 150,82 C80,78 30,70 0,52 Z"/>
      <path fill="var(--brand-blue)" d="M0,64 C200,100 450,78 700,66 C850,60 950,68 1011,86 L1011,120 L0,120 Z"/>
    </svg>
    <div class="footer-url">www.brightwellpower.com</div>
  </div>
</body>
</html>
```